Business Cards

Need business card design that I can update for new employees and details. Needs to incorporate our logo, be bright and fun (in line with tourism and holidays)
Would like a Map of Western Australia on the front with locations all the caravan parks we own (just purchased Tom Price so please include that as well as others listed on our website).
Target Market(s)
Famillies
Contact Information for Business Card
5 Cards -
Neil Perrow (Director) e: perrow@wattlebay.com.au p: 0491 570 156
Mira Perrow (Director) e: perrow@wattlebay.com.au p: 0491 570 157
Owen Halvey (General Manager) e: halvey@wattlebay.com.au p: 0491 570 158
Helen Halvey (General Manager) e: halvey@wattlebay.com.au p: 0491 570 159
Colin Danby (Training and Operations Manager) - e: danby@wattlebay.com.au p:0491 570 110
Colors
Look and feel

```html
<!DOCTYPE html>
<html lang="en">
<head>
<meta charset="utf-8">
<title>Wattlebay Tourist Parks – Business Card</title>
<link rel="stylesheet" href="https://fonts.googleapis.com/css2?family=Crimson+Text:wght@400&family=Source+Sans+3:wght@400&display=swap">
<style>
  :root {
    --backdrop: #262626;
    --card-paper: #f3f3f3;
    --brand-teal: #44c1cb;
    --brand-green: #6dbcae;
    --ink-grey: #555555;
    --ink-dark: #1e1e1e;
  }
  * { margin: 0; padding: 0; box-sizing: border-box; }
  html, body {
    width: 1200px;
    height: 900px;
    overflow: hidden;
    background: var(--backdrop);
  }
  .canvas {
    position: relative;
    width: 1200px;
    height: 900px;
  }
  .card {
    position: absolute;
    top: 170px;
    width: 347px;
    height: 561px;
    overflow: hidden;
  }
  .card--front {
    left: 259px;
    background: var(--card-paper);
    text-align: center;
  }
  .card--back {
    left: 631px;
    background: linear-gradient(180deg, var(--brand-teal) 0%, var(--brand-teal) 42%, var(--brand-green) 58%, var(--brand-green) 100%);
  }
  .brand-square {
    position: absolute;
    top: 103px;
    left: 126px;
    width: 95px;
    height: 95px;
    border: 3px solid var(--brand-teal);
  }
  .brand-name,
  .brand-tagline {
    position: absolute;
    left: 0;
    right: 0;
    font-family: "Crimson Text", "Palatino Linotype", serif;
    font-weight: 400;
    color: var(--ink-grey);
  }
  .brand-name {
    top: 196px;
    font-size: 36px;
    letter-spacing: 5px;
    line-height: 1;
    padding-left: 5px;
  }
  .brand-tagline {
    top: 238px;
    font-size: 15px;
    letter-spacing: 3.5px;
    line-height: 1;
    padding-left: 3px;
  }
  .person-name {
    position: absolute;
    top: 338px;
    left: 0;
    right: 0;
    font-family: "Crimson Text", "Palatino Linotype", serif;
    font-size: 25px;
    color: var(--brand-teal);
    line-height: 1;
  }
  .person-role {
    position: absolute;
    top: 371px;
    left: 0;
    right: 0;
    font-family: "Source Sans 3", "Myriad Pro", sans-serif;
    font-size: 16px;
    color: var(--ink-dark);
    line-height: 1;
  }
  .contact-divider {
    position: absolute;
    top: 422px;
    left: 90px;
    width: 167px;
    height: 21px;
    display: flex;
    align-items: center;
    justify-content: space-between;
  }
  .contact-divider__rule {
    width: 51px;
    height: 1px;
    background: var(--brand-teal);
  }
  .contact-divider__icons {
    display: flex;
    gap: 9px;
  }
  .contact-icon {
    width: 21px;
    height: 21px;
    background: var(--brand-teal);
    display: flex;
    align-items: center;
    justify-content: center;
  }
  .contact-details {
    position: absolute;
    top: 456px;
    left: 0;
    right: 0;
    font-family: "Source Sans 3", "Myriad Pro", sans-serif;
    font-size: 18px;
    color: var(--ink-dark);
    line-height: 25px;
  }
  .card-art {
    position: absolute;
    inset: 0;
  }
</style>
</head>
<body>
<main class="canvas">
  <section class="card card--front">
    <div class="brand-square"></div>
    <div class="brand-name">WATTLEBAY</div>
    <div class="brand-tagline">TOURIST PARKS</div>

    <div class="person-name">NEIL PERROW</div>
    <div class="person-role">Director</div>

    <div class="contact-divider">
      <span class="contact-divider__rule"></span>
      <span class="contact-divider__icons">
        <span class="contact-icon">
          <svg width="13" height="13" viewBox="0 0 24 24" aria-hidden="true">
            <path fill="#ffffff" d="M6.6 10.8a15.1 15.1 0 0 0 6.6 6.6l2.2-2.2a1 1 0 0 1 1-.25 11.4 11.4 0 0 0 3.6.57 1 1 0 0 1 1 1V20a1 1 0 0 1-1 1A17 17 0 0 1 3 4a1 1 0 0 1 1-1h3.5a1 1 0 0 1 1 1c0 1.25.2 2.45.57 3.57a1 1 0 0 1-.25 1z"/>
          </svg>
        </span>
        <span class="contact-icon">
          <svg width="13" height="10" viewBox="0 0 26 20" aria-hidden="true">
            <rect x="1" y="1" width="24" height="18" fill="none" stroke="#ffffff" stroke-width="2"/>
            <path d="M1 1l12 10L25 1" fill="none" stroke="#ffffff" stroke-width="2"/>
          </svg>
        </span>
      </span>
      <span class="contact-divider__rule"></span>
    </div>

    <div class="contact-details">
      <div class="contact-phone">0491 570 156</div>
      <div class="contact-email">perrow@wattlebay.com.au</div>
    </div>
  </section>

  <section class="card card--back">
    <div class="card-art" role="img" aria-label="Brand artwork: rising sun over a rolling green hill with birds in a teal sky"></div>
  </section>
</main>
</body>
</html>
```